Upmarket Dessert Lounge needs a Business Card Design

We are an upmarket dessert lounge needing a business card to match our image.

We want something that is simple yet beautiful, feminine, classy, sophisticated and elegant. We want it to stand out and don't mind if it is bold.

The design should include our logo and colours of red or maroon with gold highlights. We don't mind if black is used.

Marlow & Quince

Target Market(s)

For those who like to indulge or treat themselves and give in to their temptations on good quality desserts.

Industry/Entity Type

Business

Requirements
Must have
• Must include our logo and our name

Marlow & Quince

M & Q

```html
<!DOCTYPE html>
<html lang="en">
<head>
<meta charset="utf-8">
<title>Marlow &amp; Quince — Business Card</title>
<link rel="stylesheet" href="https://fonts.googleapis.com/css2?family=Open+Sans:wght@400;700&display=swap">
<style>
  :root {
    --backdrop: #d9d9d9;
    --card-black: #000000;
    --cream: #fdd49b;
    --maroon: #7a1315;
    --ink-dark: #3a3a3a;
    --text-light: #ffffff;
  }
  * { margin: 0; padding: 0; box-sizing: border-box; }
  html, body {
    width: 956px;
    height: 1200px;
    overflow: hidden;
  }
  body {
    position: relative;
    background: var(--backdrop);
    font-family: "Open Sans", Arial, sans-serif;
  }
  .card {
    position: absolute;
    left: 74px;
    width: 798px;
    background: var(--card-black);
    border-radius: 28px;
    overflow: hidden;
    box-shadow: 0 6px 14px rgba(0,0,0,0.35);
  }
  .card--front { top: 97px; height: 454px; }
  .card--back  { top: 632px; height: 455px; }

  .brand {
    position: absolute;
    left: 0;
    width: 100%;
    display: flex;
    align-items: center;
    justify-content: center;
    white-space: nowrap;
  }
  .brand-mark {
    flex: none;
    background: var(--maroon);
    border: 2px solid var(--cream);
  }
  .brand-name {
    color: var(--cream);
    font-weight: 400;
    text-transform: uppercase;
  }
  .card--front .brand { top: 92px; gap: 16px; }
  .card--front .brand-mark { width: 22px; height: 22px; }
  .card--front .brand-name { font-size: 32px; letter-spacing: 2px; }

  .card--back .brand { top: 160px; gap: 30px; }
  .card--back .brand-mark { width: 44px; height: 44px; border-width: 3px; }
  .card--back .brand-name { font-size: 100px; line-height: 1.1; }

  .title-band {
    position: absolute;
    top: 234px;
    left: 0;
    width: 684px;
    height: 53px;
    background: var(--cream);
    color: var(--ink-dark);
    font-size: 24px;
    line-height: 53px;
    text-align: center;
    padding-left: 120px;
  }
  .title-band .person { font-weight: 700; }
  .title-band-accent {
    position: absolute;
    top: 234px;
    left: 694px;
    width: 104px;
    height: 53px;
    background: var(--maroon);
  }

  .contact-list {
    position: absolute;
    top: 302px;
    left: 126px;
    list-style: none;
    color: var(--text-light);
    font-size: 17.6px;
    line-height: 28px;
  }
  .contact-list b { font-weight: 700; }

  .address {
    position: absolute;
    top: 388px;
    left: 433px;
    color: var(--text-light);
    font-size: 19.5px;
    line-height: 28px;
    font-style: normal;
  }
</style>
</head>
<body>
  <section class="card card--front" aria-label="Card front">
    <div class="brand">
      <span class="brand-mark" aria-hidden="true"></span>
      <span class="brand-name">Marlow &amp; Quince</span>
    </div>
    <div class="title-band"><span class="person">Your Name -</span> Designation</div>
    <div class="title-band-accent"></div>
    <ul class="contact-list">
      <li><b>p</b> : 123-456-7890</li>
      <li><b>c</b> : 123-456-7890</li>
      <li><b>f</b> : 123-456-7890</li>
      <li><b>e</b> : name@yourwebsite.com</li>
      <li><b>w</b> : www.marlowquince.com</li>
    </ul>
    <address class="address">0000, Street Name<br>City Name, Country Code.</address>
  </section>

  <section class="card card--back" aria-label="Card back">
    <div class="brand">
      <span class="brand-mark" aria-hidden="true"></span>
      <span class="brand-name">M &amp; Q</span>
    </div>
  </section>
</body>
</html>
```